Software Product Flyer Design

A established czech software company needs a marketing flyer to promote their software product and its modules.
The overall feel of the flyer must to be serious, but also eye-catching, enticing, clever and bold to attract customers.
Unifying graphic element is the new product logo.
The flyer would be A4, colour both sides and folded once (to give 4 pages of A5).
Title page - product logo with module name and module icon, short presentation of the product and list of its key features.
Inside pages - detailed informations with screenshots or graphical schemas.
Back side - informations about technical requirements and user support, contacts (address, phone, fax, e-mail, web pages - no social networks).
Product logo, module icon and some images attached.
Updates
Hello,
Reason: For organizational reasons we extending the deadline by 10 days.
FYI: We have uploaded the new ZIP file with previous version of our flyer.
Attached PDF file with text for inner pages.
Target Market(s)
Existing or new customers like municipalities, public authorities and nonprofit organizations.
Industry/Entity Type
Marketing
Requirements
Must have
- Winning designer must provide a template for Adobe InDesign based on his graphic design.
Avoid to using exotic fonts - in Czech we use Latin Extended characters (like áéěíýůčřžšťďň).
Nice to have
- Using graphic motif from product logo like as attached splash screen.

```html
<!DOCTYPE html>
<html lang="en">
<head>
<meta charset="utf-8">
<title>Velnor – Module Flyer, Back and Front</title>
<link rel="stylesheet" href="https://fonts.googleapis.com/css2?family=Source+Sans+3:wght@400;600;700&display=swap">
<style>
  :root {
    --paper: #ffffff;
    --ink: #2b2d31;
    --ink-soft: #3a3d42;
    --panel-top: #3b3f44;
    --panel-bottom: #141618;
    --accent: #f05a22;
    --grey: #9a9fa3;
    --fold: #d9dadb;
    --tab: #4a4f55;
    --light-text: #f2f2f2;
  }
  * { box-sizing: border-box; margin: 0; padding: 0; }
  html, body { width: 1200px; height: 889px; overflow: hidden; background: var(--paper); }
  body { font-family: "Source Sans 3", "Helvetica Neue", Arial, sans-serif; color: var(--ink); }

  .flyer { position: relative; width: 1200px; height: 889px; background: var(--paper); }
  .page { position: absolute; top: 0; height: 889px; }
  .page--back { left: 0; width: 602px; }
  .page--front { left: 603px; width: 597px; }
  .fold-line { position: absolute; left: 602px; top: 0; width: 1px; height: 889px; background: var(--fold); }

  /* Back page */
  .support-panel {
    position: absolute; left: 0; top: 200px; width: 602px; height: 513px;
    background: linear-gradient(135deg, var(--panel-top) 0%, #24272a 55%, var(--panel-bottom) 100%);
    padding: 46px 0 0 70px;
  }
  .support-title { color: var(--accent); font-weight: 400; font-size: 31px; letter-spacing: 0.3px; margin-left: 0; }
  .support-text {
    margin-top: 26px; margin-left: -5px; width: 500px;
    color: var(--light-text); font-size: 15.6px; line-height: 33px;
  }

  .contact-mark { position: absolute; left: 170px; top: 760px; display: flex; align-items: center; gap: 10px; }
  .contact-mark__square { width: 28px; height: 28px; background: var(--accent); border-radius: 6px; }
  .contact-mark__name { font-size: 26px; font-weight: 700; color: var(--ink-soft); }
  .contact-list { position: absolute; left: 289px; top: 748px; list-style: none; font-size: 16px; line-height: 21.5px; color: var(--ink); }
  .contact-address { position: absolute; left: 0; width: 602px; top: 840px; text-align: center; font-size: 15.5px; color: var(--ink); }

  /* Front page */
  .brand { position: absolute; left: 180px; top: 70px; display: flex; align-items: center; gap: 14px; }
  .brand__square { width: 40px; height: 40px; background: var(--accent); border-radius: 8px; }
  .brand__name { font-size: 84px; font-weight: 700; line-height: 1; color: var(--ink-soft); letter-spacing: -1px; }

  .module-icon-art {
    position: absolute; left: 40px; top: 150px; width: 520px; height: 560px;
    background: radial-gradient(circle at 54% 50%, #1c1e20 0%, #2c2f33 26%, #dfe3e6 44%, #f3f5f6 62%, var(--paper) 80%);
  }
  .module-name {
    position: absolute; left: 169px; top: 730px;
    font-size: 31px; font-weight: 400; letter-spacing: 5px; color: var(--ink);
  }
  .front-web {
    position: absolute; left: 219px; top: 840px;
    font-size: 16px; font-weight: 700; letter-spacing: 2.5px; color: var(--ink);
  }
  .inner-tab {
    position: absolute; right: 0; top: 198px; width: 20px; height: 513px;
    background: var(--tab); border-radius: 20px 0 0 20px;
  }
</style>
</head>
<body>
<main class="flyer">
  <section class="page page--back">
    <div class="support-panel">
      <h2 class="support-title">USER SUPPORT</h2>
      <p class="support-text">Lorem ipsum dolor sit amet, consectetuer adipiscing elit, sed diam nonummy nibh euismod tincidunt ut laoreet dolore magna aliquam erat volutpat. Ut wisi enim ad minim veniam, quis nostrud exerci tation ullamcorper suscipit lobortis nisl ut aliquip ex ea commodo consequat. Duis autem vel eum iriure dolor in hendrerit in vulputate velit esse molestie consequat, vel illum dolore eu feugiat nulla facilisis at vero eros et accumsan et iusto odio dignissim qui blandit praesent luptatum zzril delenit augue duis dolore te feugait nulla facilisi.</p>
    </div>
    <div class="contact-mark">
      <span class="contact-mark__square"></span>
      <span class="contact-mark__name">velnor</span>
    </div>
    <ul class="contact-list">
      <li>P : 012 - 456 - 7890</li>
      <li>F : 012 - 456 - 7890</li>
      <li>E :&nbsp; info@velnor.com</li>
    </ul>
    <p class="contact-address">Suite 000 Cityname, Countryname 0000 00</p>
  </section>

  <div class="fold-line"></div>

  <section class="page page--front">
    <div class="module-icon-art" role="img" aria-label="Module icon: a processor chip with circuit traces, showing a notebook with the letter A and a pencil"></div>
    <div class="brand">
      <span class="brand__square"></span>
      <span class="brand__name">velnor</span>
    </div>
    <p class="module-name">module name</p>
    <p class="front-web">www.velnor.com</p>
    <div class="inner-tab"></div>
  </section>
</main>
</body>
</html>
```